Local Roofing/Construction company business needs new biz card design

We need a new business card design, current cards are from the start of this operation and generic at best. We are a local Construction Company (General Contractor) with a majority of our work originating from insurance claims-exterior finish work is the main focus (Roofs-Siding-Gutters etc). Heavily involved with homeowners and the low ball offers they receive from insurance company's after a insurable event takes place. I have attached some of our original logo file(s) below.

```html
<!DOCTYPE html>
<html lang="en">
<head>
<meta charset="utf-8">
<title>Stonefield Construction – Business Card</title>
<link rel="stylesheet" href="https://fonts.googleapis.com/css2?family=Poppins:wght@400;600;700&display=swap">
<style>
  :root {
    --bg: #2a2a2a;
    --card: #0c0c0c;
    --green: #33d67e;
    --text-grey: #c9c9c9;
    --rule: #4a4a4a;
    --white: #f4f4f4;
  }
  * { box-sizing: border-box; margin: 0; padding: 0; }
  html, body {
    width: 1200px; height: 900px; overflow: hidden;
    background: var(--bg);
    font-family: "Poppins", sans-serif;
  }
  .canvas {
    width: 1200px; height: 900px;
    display: flex; flex-direction: column; align-items: center; justify-content: center;
    gap: 56px;
  }
  .card {
    width: 600px; height: 343px;
    background: var(--card);
    border-radius: 22px;
    position: relative;
    box-shadow: 0 18px 40px rgba(0,0,0,.45);
  }
  /* Front */
  .card-front { display: flex; align-items: center; padding: 0 40px 0 48px; }
  .brand {
    width: 210px; display: flex; align-items: center; gap: 12px;
  }
  .brand-square {
    width: 22px; height: 22px; background: var(--green); flex: none; border-radius: 3px;
  }
  .brand-name {
    color: var(--green); font-weight: 700; font-size: 20px; line-height: 1.15;
    text-transform: uppercase; letter-spacing: .5px;
  }
  .divider {
    width: 1px; height: 190px; background: var(--rule); margin: 0 30px 0 26px; flex: none;
  }
  .details { color: var(--text-grey); }
  .person-name {
    color: var(--green); font-weight: 700; font-size: 22px; letter-spacing: .5px;
    text-transform: uppercase; line-height: 1.1;
  }
  .person-title { font-size: 15px; margin-bottom: 14px; }
  .contact-list { list-style: none; font-size: 15px; line-height: 1.55; }
  .contact-list li { display: flex; align-items: center; gap: 9px; }
  .contact-list svg { width: 14px; height: 14px; flex: none; }
  .address { font-size: 15px; line-height: 1.45; margin-top: 14px; padding-left: 23px; }
  /* Back */
  .card-back { display: flex; align-items: center; justify-content: center; }
  .back-name {
    color: var(--white); font-weight: 700; font-size: 34px; letter-spacing: 1px;
    text-transform: uppercase;
  }
</style>
</head>
<body>
<main class="canvas">
  <section class="card card-front">
    <div class="brand">
      <span class="brand-square"></span>
      <span class="brand-name">Stonefield Construction</span>
    </div>
    <div class="divider"></div>
    <div class="details">
      <p class="person-name">Dana Whitfield</p>
      <p class="person-title">Managing Director</p>
      <ul class="contact-list">
        <li>
          <svg viewBox="0 0 24 24" fill="var(--green)"><path d="M6.6 10.8a15.1 15.1 0 0 0 6.6 6.6l2.2-2.2a1 1 0 0 1 1-.25 11.4 11.4 0 0 0 3.6.57 1 1 0 0 1 1 1V20a1 1 0 0 1-1 1A17 17 0 0 1 3 4a1 1 0 0 1 1-1h3.5a1 1 0 0 1 1 1c0 1.25.2 2.45.57 3.6a1 1 0 0 1-.25 1z"/></svg>
          044-555 019 284
        </li>
        <li>
          <svg viewBox="0 0 24 24" fill="var(--green)"><path d="M2 5h20v14H2z"/><path d="M2 5l10 8 10-8" stroke="#0c0c0c" stroke-width="2" fill="none"/></svg>
          info@stonefieldbuild.com
        </li>
        <li>
          <svg viewBox="0 0 24 24" fill="none" stroke="var(--green)" stroke-width="2"><circle cx="12" cy="12" r="10"/><path d="M2 12h20M12 2c3 3 3 17 0 20M12 2c-3 3-3 17 0 20"/></svg>
          www.stonefieldbuild.com
        </li>
      </ul>
      <p class="address">421, Address line goes here<br>45452, Country Name</p>
    </div>
  </section>

  <section class="card card-back">
    <p class="back-name">Stonefield</p>
  </section>
</main>
</body>
</html>
```